Simplified minimalist but bold website

Design a website for a brand 'Brighten Every Day' that shares ideas to make managing home and health easier through email swap series, webinars and eventually courses.

Simple landing page to attract users to sign up for a freebie.

Target Market(s)

women with families & homes to run

Number of Pages Required

1 page

Font styles to use
Sans Serif

Colors
e667a6
b768aa
acd136
ffffff
959595

Requirements
Must have
• Simplified look, line icons, opt-in template, contact us form

```html
<!DOCTYPE html>
<html lang="en">
<head>
<meta charset="utf-8">
<title>Brighten Every Day</title>
<link href="https://fonts.googleapis.com/css2?family=Raleway:wght@300;400;600;700&display=swap" rel="stylesheet">
<style>
:root{
  --pink:#e667a6;
  --purple:#b768aa;
  --green:#acd136;
  --white:#ffffff;
  --grey:#959595;
  --blue:#2f8fd6;
  --ink:#555555;
}
*{box-sizing:border-box;margin:0;padding:0}
html,body{width:758px;height:1200px;overflow:hidden}
body{font-family:'Raleway',Arial,sans-serif;color:var(--ink);background:var(--white)}
.page{width:758px;height:1200px;position:relative}

/* hero */
.hero{height:467px;position:relative;text-align:center;color:var(--white);
  background:linear-gradient(135deg,#e86aa8 0%,#d46cb0 45%,#b88bd0 75%,#c9a7da 100%)}
.hero-photo{position:absolute;inset:0;
  background:radial-gradient(ellipse at 62% 78%,rgba(255,235,220,.35),transparent 55%),
             radial-gradient(ellipse at 20% 70%,rgba(120,200,140,.25),transparent 40%)}
.hero-content{position:relative;padding-top:70px}
.hero-title{font-weight:300;font-size:46px;letter-spacing:.5px}
.hero-rule{width:240px;height:1px;background:rgba(255,255,255,.8);margin:14px auto 14px}
.hero-sub{font-weight:300;font-size:24px;line-height:30px}
.hero-arrow{margin-top:48px}

/* offers */
.offers{display:flex;height:291px}
.offer{flex:1;text-align:center;padding-top:22px}
.offer-light{background:var(--white)}
.offer-green{background:var(--green);color:var(--white)}
.offer-kicker{font-size:10px;color:var(--grey)}
.offer-green .offer-kicker{color:var(--white)}
.offer-title{font-weight:400;font-size:20px;margin-top:16px;color:var(--ink)}
.offer-green .offer-title{color:var(--white)}
.offer-rule{width:46px;height:2px;background:var(--green);margin:6px auto 8px}
.offer-green .offer-rule{background:var(--white)}
.offer-text{font-size:8px;line-height:11px;width:270px;margin:0 auto;color:var(--ink)}
.offer-actions{display:flex;justify-content:center;gap:10px;margin:12px 0 10px}
.btn-outline{border:1.5px solid var(--green);border-radius:12px;font-size:7px;font-weight:700;
  padding:5px 12px;color:var(--ink);letter-spacing:.3px}
.offer-prompt{font-size:11px;font-weight:600;color:var(--purple);margin-bottom:8px}
.field{display:block;width:210px;height:20px;border:1px solid var(--pink);border-radius:10px;
  margin:0 auto 8px;text-align:left;padding-left:12px;font-size:8px;line-height:18px;color:var(--grey)}
.offer-green .field{border-color:var(--white);color:var(--white)}
.btn-solid{display:block;width:210px;height:22px;margin:10px auto 0;border-radius:11px;
  background:var(--pink);color:var(--white);font-size:8px;font-weight:700;line-height:22px;letter-spacing:.4px}
.guide-art{width:150px;height:98px;margin:8px auto 12px;border-radius:6px;
  background:linear-gradient(135deg,#f2f5e6,#dfe9b8)}

/* series */
.series{height:404px;position:relative;text-align:center;
  background:linear-gradient(180deg,#dfe6ee 0%,#eef1f5 40%,#e5e9ef 100%)}
.series-photo{position:absolute;inset:0;
  background:radial-gradient(ellipse at 78% 40%,rgba(190,170,200,.35),transparent 50%),
             radial-gradient(ellipse at 25% 60%,rgba(200,205,215,.5),transparent 50%)}
.series-body{position:relative;padding-top:44px}
.series-title{font-weight:300;font-size:30px;color:var(--blue)}
.series-rule{width:60px;height:2px;background:var(--blue);margin:10px auto 16px}
.series-text{font-size:9px;line-height:13px;width:360px;margin:0 auto 12px;color:var(--ink)}
.btn-blue{display:inline-block;width:210px;height:26px;margin-top:16px;border-radius:13px;
  background:var(--blue);color:var(--white);font-size:9px;font-weight:700;line-height:26px;letter-spacing:.4px}

/* footer */
.footer{height:38px;background:var(--pink);color:var(--white);text-align:center;
  font-size:8px;line-height:38px}
</style>
</head>
<body>
<div class="page">

  <header class="hero">
    <div class="hero-photo" role="img" aria-label="Woman relaxing at a laptop in a bright home, tinted pink and purple"></div>
    <div class="hero-content">
      <h1 class="hero-title">Brighten Every Day</h1>
      <div class="hero-rule"></div>
      <p class="hero-sub">Chances are life is a little overwhelming.<br>Let us help.</p>
      <svg class="hero-arrow" width="24" height="30" viewBox="0 0 24 30" fill="none" stroke="#fff" stroke-width="2">
        <line x1="12" y1="2" x2="12" y2="27"/><polyline points="3,18 12,27 21,18"/>
      </svg>
    </div>
  </header>

  <section class="offers">
    <div class="offer offer-light">
      <p class="offer-kicker">Baby Steps... (try out a few of our tricks)</p>
      <h2 class="offer-title">Swaps Email Series</h2>
      <div class="offer-rule"></div>
      <p class="offer-text">Save TIME, MONEY and SANITY with simple product swaps. Reduce the amount of work it takes to run your home. Swap out existing products for more sustainable ones. Each swap saves you work, clutter, time &amp; money.</p>
      <div class="offer-actions">
        <span class="btn-outline">SEE SAMPLE SWAPS</span>
        <span class="btn-outline">LEARN MORE</span>
      </div>
      <p class="offer-prompt">Send your ideas my way...</p>
      <span class="field">Name</span>
      <span class="field">Email</span>
      <span class="btn-solid">SEND ME THE GUIDE</span>
    </div>
    <div class="offer offer-green">
      <p class="offer-kicker">Big Leap... (I'm ready to roll up my sleeves)</p>
      <h2 class="offer-title">Decluttering Guide</h2>
      <div class="guide-art" role="img" aria-label="Decluttering guide booklets"></div>
      <span class="field">Name</span>
      <span class="field">Email</span>
      <span class="btn-solid">SIGN ME UP!</span>
    </div>
  </section>

  <section class="series">
    <div class="series-photo" role="img" aria-label="Softly blurred photo of a tidy family living room"></div>
    <div class="series-body">
      <h2 class="series-title">Swaps Email Series</h2>
      <div class="series-rule"></div>
      <p class="series-text">Save TIME, MONEY and SANITY with simple product swaps and reduce the amount of work it takes to run your home. Swap out existing products for more sustainable ones. Each swap saves you work, clutter, time &amp; money.</p>
      <p class="series-text">You get an email (or swap) for 10 weeks, one at a time, so you can see if they are helpful to you.</p>
      <p class="series-text">Join our monthly SIMPLE SWAP SHARING with parents who share tips and gain new ideas. Better yet, come with great tips of your own to share!</p>
      <span class="btn-blue">SIGN ME UP!</span>
    </div>
  </section>

  <footer class="footer">© 2018 Company Name. All rights reserved.</footer>

</div>
</body>
</html>
```